Meridale Nutrition needs Stationary and a business card

We would like to use our current logo. The text can be moved around as needed. The stationary needs to be a 'first page' where the logo is more prominent to be impressive on higher quality paper and a second page where the logo is more subtle where there will be much more information on the page. There are 2 clinic locations which will need include name, address, phone number, fax number, web address. The business card should be single sided and contain this information also.
The design must be contemporary and sophisticated as this is a science based diet run out of a medical clinic.

Target Market(s)

People wanting to lose weight, athletes looking to optimise performance, people with arthritis or fighting cancer

Industry/Entity Type

Business

Contact Information for Business Card

must use the logo. I have attached an example card with the practice details on it. there must be space for the doctors name. Also the website www.meridalenutrition.com.au

Requirements
Must have
• the logo, the business adresses and phone numbers, the website, the doctors name and qualifications
Nice to have
• some creativity
Should not have
• Do not simply reproduce the existing card please

```html
<!DOCTYPE html>
<html lang="en">
<head>
<meta charset="utf-8">
<title>Meridale Nutrition – Business Card</title>
<link rel="stylesheet" href="https://fonts.googleapis.com/css2?family=Arimo:wght@400;700&display=swap">
<style>
  :root {
    --page-bg: #e4e6e9;
    --card-white: #ffffff;
    --card-grey: #eceef0;
    --panel-blue: #2c5f93;
    --accent-cyan: #19b4ea;
    --brand-navy: #2b4f7c;
    --text-light: #ffffff;
  }
  html, body {
    margin: 0;
    width: 1200px;
    height: 950px;
    overflow: hidden;
    background: var(--page-bg);
    font-family: "Arimo", Arial, sans-serif;
  }
  .sheet {
    position: relative;
    width: 1200px;
    height: 950px;
  }
  .card {
    position: absolute;
    left: 250px;
    width: 700px;
    height: 400px;
    background: linear-gradient(160deg, var(--card-white) 55%, var(--card-grey));
    box-shadow: 0 6px 18px rgba(0,0,0,0.18);
    overflow: hidden;
  }
  .card--back { top: 50px; }
  .card--front { top: 500px; }

  .card__shape {
    position: absolute;
    inset: 0;
  }

  .brand {
    position: absolute;
    display: flex;
    align-items: center;
    gap: 14px;
  }
  .brand__dot {
    width: 54px;
    height: 54px;
    border-radius: 50%;
    background: var(--accent-cyan);
    flex: none;
  }
  .brand__name {
    font-weight: 700;
    font-size: 30px;
    color: var(--brand-navy);
    letter-spacing: 0.5px;
    white-space: nowrap;
  }
  .card--back .brand {
    left: 50%;
    top: 50%;
    transform: translate(-50%, -50%);
  }
  .card--front .brand {
    left: 418px;
    top: 200px;
    flex-direction: column;
    gap: 14px;
  }
  .card--front .brand__dot { width: 110px; height: 110px; }
  .card--front .brand__name { font-size: 27px; }

  .details {
    position: absolute;
    left: 30px;
    top: 28px;
    color: var(--text-light);
    line-height: 1.22;
  }
  .details__name {
    margin: 0 0 4px;
    font-size: 25px;
    font-weight: 700;
  }
  .details__quals {
    margin: 0 0 12px;
    font-size: 14px;
  }
  .clinic {
    margin: 0 0 12px;
    font-size: 16px;
    font-style: normal;
  }
  .clinic__name { font-weight: 700; display: block; }
  .clinic__tel b { font-weight: 700; }
  .details__web {
    font-size: 16px;
    margin: 6px 0 0;
  }
</style>
</head>
<body>
<main class="sheet">

  <section class="card card--back" aria-label="Business card back">
    <div class="brand">
      <span class="brand__dot"></span>
      <span class="brand__name">Meridale Nutrition</span>
    </div>
  </section>

  <section class="card card--front" aria-label="Business card front">
    <svg class="card__shape" viewBox="0 0 700 400" width="700" height="400" aria-hidden="true">
      <path d="M0 0 H372 Q300 190 322 400 H0 Z" fill="var(--panel-blue)"/>
      <path d="M383 0 Q311 190 333 400" fill="none" stroke="var(--accent-cyan)" stroke-width="5"/>
    </svg>

    <div class="details">
      <h1 class="details__name">Dr Elias Varden</h1>
      <p class="details__quals">MBBS (NSW)<br>MBiomedE<br>FRACS (Ortho)<br>FAOrthA Orthopaedic Surgeon</p>

      <address class="clinic">
        <span class="clinic__name">Harwell</span>
        52-54 Linden Road<br>
        Harwell NSW 2140<br>
        <span class="clinic__tel"><b>Tel:</b> 02 9100 4821</span>
      </address>

      <address class="clinic">
        <span class="clinic__name">Ashcombe</span>
        168 Marlow Road<br>
        Ashcombe NSW 2034<br>
        <span class="clinic__tel"><b>Tel:</b> 02 9100 7350</span>
      </address>

      <p class="details__web">www.meridalenutrition.com.au</p>
    </div>

    <div class="brand" style="left:400px; top:95px; width:280px; align-items:center;">
      <span class="brand__dot"></span>
      <span class="brand__name">Meridale Nutrition</span>
    </div>
  </section>

</main>
</body>
</html>
```